Packaging sleeve for food containers

I have designed eco-friendly food prep containers that come in packs of 10. The food containers are beige with a clear lid. I need a design for a cardboard sleeve that wraps around the containers as part of the packaging with all of the information on it. I will upload a basic idea of what I am looking for as well as 2 other similar brands for comparison. I have a template with the information I require to be included but I need the final design to be jazzed up to a professional standard. I need help with colours and the design of the sleeve.

Target Market(s)

People who like to meal prep their food in advance and who might also be environmentally conscious. Female and male, somewhat health conscious. Might be looking to lose or maintain weight or just improve nutrition. Organised people. Age range 20-50(ish).

Font styles to use
Serif
Sans Serif

Requirements
Must have
• The information contained in my example sleeve
Nice to have
• Harmonious colours

```html
<!DOCTYPE html>
<html lang="en">
<head>
<meta charset="utf-8">
<title>Lunchwell – Meal Prep Container Sleeve</title>
<link rel="stylesheet" href="https://fonts.googleapis.com/css2?family=Archivo+Black&family=Open+Sans:wght@400;600;700&display=swap">
<style>
:root{
  --backdrop:#e8efe4;
  --sleeve:#f9b11f;
  --pattern:#f3a81a;
  --green:#137236;
  --white:#ffffff;
  --cut:#3a8fc2;
  --display:"Archivo Black",sans-serif;
  --body:"Open Sans",sans-serif;
}
*{box-sizing:border-box;margin:0;padding:0}
html,body{width:1200px;height:1059px;overflow:hidden;background:var(--backdrop)}
.canvas{position:relative;width:1200px;height:1059px}
.panel{position:absolute;background:var(--sleeve);border:1px solid var(--cut);overflow:hidden}
.pattern{position:absolute;inset:0;background:radial-gradient(circle at 50% 50%,var(--sleeve),var(--pattern))}
.abs{position:absolute}
.center{left:0;right:0;text-align:center}
.brand-name{position:absolute;display:flex;align-items:center;justify-content:center;gap:.35em;font-family:var(--body);font-weight:700;letter-spacing:.01em;white-space:nowrap}
.brand-name.light{color:var(--white)}
.brand-name.dark{color:var(--green)}
.brand-name .mark{display:inline-block;width:.5em;height:.5em;border-radius:50%;background:currentColor}
.pack-badge{position:absolute;border-radius:50%;background:var(--white);border:3px solid var(--green);color:var(--green);font-family:var(--body);font-weight:600;display:flex;align-items:center;justify-content:center;text-align:center;line-height:1}
.title-green{font-family:var(--display);color:var(--green);letter-spacing:.02em}
.title-white{font-family:var(--display);color:var(--white);letter-spacing:.02em}
.subtitle{font-family:var(--display);white-space:nowrap}
.subtitle .g{color:var(--green)}.subtitle .w{color:var(--white)}
.compart{font-family:var(--body);font-weight:700;color:var(--white);letter-spacing:.04em}
.web-band{position:absolute;left:0;right:0;background:var(--green);color:var(--white);font-family:var(--body);text-align:center;letter-spacing:.06em}
.features{position:absolute;border:2px solid var(--white);display:grid;grid-template-columns:repeat(3,1fr);grid-template-rows:repeat(3,1fr)}
.feature{display:flex;flex-direction:column;align-items:center;justify-content:center;color:var(--white);font-family:var(--body);font-weight:700;text-align:center;line-height:1}
.feature svg{display:block}
.flap-text{position:absolute;inset:0;transform:rotate(180deg);color:var(--white);font-family:var(--body);font-size:7.5px;text-align:center}
.flap-text p{position:absolute;left:0;right:0}
.dot{display:inline-block;width:8px;height:8px;border-radius:50%;background:var(--white);vertical-align:-1px;margin-left:4px}
</style>
</head>
<body>
<div class="canvas">

  <section class="panel" style="left:62px;top:84px;width:242px;height:893px;background:var(--white)">
    <div class="panel" style="left:-1px;top:-1px;width:242px;height:182px">
      <div class="pattern" role="img" aria-label="Faint food doodle pattern"></div>
      <div class="flap-text">
        <p style="top:57px">Winner Winner Meal Prep dinner!</p>
        <p style="top:71px">Tag us @Lunchwell on <span class="dot"></span> with</p>
        <p style="top:85px">your containers to win monthly prizes</p>
        <p style="top:141px">Connect with us</p>
        <p style="top:156px">www.lunchwell.com.au</p>
        <p style="top:170px">@Lunchwell <span class="dot"></span></p>
      </div>
    </div>
    <div class="panel" style="left:-1px;top:180px;width:242px;height:281px">
      <div class="pattern" role="img" aria-label="Faint food doodle pattern"></div>
      <div class="brand-name light" style="left:40px;width:166px;top:50px;height:30px;font-size:18px"><span class="mark"></span>Lunchwell</div>
      <div class="pack-badge" style="left:191px;top:15px;width:43px;height:43px;font-size:10px">10<br>Pack</div>
      <div class="abs center title-green" style="top:125px;font-size:19px">Meal Prep</div>
      <div class="abs center title-white" style="top:148px;font-size:18px">CONTAINERS</div>
      <div class="abs center subtitle" style="top:183px;font-size:15px"><span class="g">Eco Friendly</span> <span class="w">Wheatstraw</span></div>
      <div class="abs center compart" style="top:210px;font-size:13px">3 compartment</div>
      <svg class="abs" style="left:104px;top:236px" width="43" height="30" viewBox="0 0 43 30">
        <rect x="1" y="1" width="41" height="28" fill="none" stroke="var(--green)" stroke-width="1.5"/>
        <rect x="4" y="4" width="16" height="22" rx="4" fill="none" stroke="var(--green)" stroke-width="1.5"/>
        <rect x="23" y="4" width="16" height="10" rx="4" fill="none" stroke="var(--green)" stroke-width="1.5"/>
        <rect x="23" y="16" width="16" height="10" rx="4" fill="none" stroke="var(--green)" stroke-width="1.5"/>
        <g font-family="Archivo Black,sans-serif" font-size="7" fill="var(--white)" text-anchor="middle">
          <text x="12" y="18">2c</text><text x="31" y="12">1c</text><text x="31" y="24">1c</text>
        </g>
      </svg>
    </div>
    <div class="panel" style="left:-1px;top:460px;width:242px;height:182px">
      <div class="pattern" role="img" aria-label="Faint food doodle pattern"></div>
      <div class="features" style="left:45px;top:24px;width:148px;height:139px">
        <div class="feature" style="font-size:4px"><svg width="26" height="26" viewBox="0 0 26 26"><circle cx="13" cy="13" r="11.5" fill="none" stroke="#fff" stroke-width="1.5"/><rect x="6" y="8" width="14" height="10" rx="1" fill="none" stroke="#fff"/></svg>Microwave Safe</div>
        <div class="feature" style="font-size:4px"><svg width="26" height="26" viewBox="0 0 26 26"><circle cx="13" cy="13" r="11.5" fill="none" stroke="#fff" stroke-width="1.5"/><path d="M13 5v16M6 9l14 8M6 17l14-8" stroke="#fff"/></svg>Freezer Safe</div>
        <div class="feature" style="font-size:4px"><svg width="26" height="26" viewBox="0 0 26 26"><circle cx="13" cy="13" r="11.5" fill="none" stroke="#fff" stroke-width="1.5"/><circle cx="11" cy="15" r="4" fill="none" stroke="#fff"/><circle cx="16" cy="15" r="4" fill="none" stroke="#fff"/></svg>Dishwasher Safe</div>
        <div class="feature" style="font-size:4px"><svg width="26" height="26" viewBox="0 0 26 26"><circle cx="13" cy="13" r="11.5" fill="none" stroke="#fff" stroke-width="1.5"/><text x="13" y="13" font-size="6" fill="#fff" text-anchor="middle" font-family="Open Sans,sans-serif">BPA</text><text x="13" y="19" font-size="5" fill="#fff" text-anchor="middle" font-family="Open Sans,sans-serif">FREE</text></svg>BPA Free</div>
        <div class="feature" style="font-size:4px"><svg width="26" height="26" viewBox="0 0 26 26"><circle cx="13" cy="13" r="11.5" fill="none" stroke="#fff" stroke-width="1.5"/><path d="M13 21V7M13 11l-3-3M13 14l3-3" stroke="#fff" fill="none"/></svg>Wheatstraw</div>
        <div class="feature" style="font-size:4px"><svg width="26" height="26" viewBox="0 0 26 26"><circle cx="13" cy="13" r="11.5" fill="none" stroke="#fff" stroke-width="1.5"/><path d="M13 7l5 9a5 5 0 0 1-10 0z" fill="none" stroke="#fff"/><path d="M5 19L21 7" stroke="#fff"/></svg>Leakproof</div>
        <div class="feature" style="font-size:4px"><svg width="26" height="26" viewBox="0 0 26 26"><circle cx="13" cy="13" r="11.5" fill="none" stroke="#fff" stroke-width="1.5"/><path d="M4 10h18M3 13h20M4 16h18" stroke="#fff"/></svg>Stackable</div>
        <div class="feature" style="font-size:4px"><svg width="26" height="26" viewBox="0 0 26 26"><circle cx="13" cy="13" r="11.5" fill="none" stroke="#fff" stroke-width="1.5"/><g fill="none" stroke="#fff" stroke-width=".8"><circle cx="8" cy="10" r="2.5"/><circle cx="13" cy="10" r="2.5"/><circle cx="18" cy="10" r="2.5"/><circle cx="8" cy="16" r="2.5"/><circle cx="13" cy="16" r="2.5"/><circle cx="18" cy="16" r="2.5"/></g></svg>Reusable</div>
        <div class="feature" style="font-size:4px"><svg width="26" height="26" viewBox="0 0 26 26"><circle cx="13" cy="13" r="11.5" fill="none" stroke="#fff" stroke-width="1.5"/><path d="M13 6l6 11H7z" fill="none" stroke="#fff" stroke-width="1.5"/></svg>Recycle</div>
      </div>
    </div>
    <div class="panel" style="left:-1px;top:641px;width:242px;height:223px">
      <div class="pattern" role="img" aria-label="Faint food doodle pattern"></div>
      <div class="brand-name dark" style="left:0;width:242px;top:93px;height:30px;font-size:18px"><span class="mark"></span>Lunchwell</div>
      <div class="web-band" style="top:183px;height:19px;line-height:19px;font-size:10px">www.lunchwell.com.au</div>
    </div>
  </section>

  <section class="panel" style="left:333px;top:203px;width:459px;height:536px">
    <div class="pattern" role="img" aria-label="Faint food doodle pattern"></div>
    <div class="brand-name light" style="left:90px;width:296px;top:100px;height:50px;font-size:36px"><span class="mark"></span>Lunchwell</div>
    <div class="pack-badge" style="left:367px;top:32px;width:78px;height:78px;font-size:20px">10<br>Pack</div>
    <div class="abs center title-green" style="top:236px;font-size:38px">Meal Prep</div>
    <div class="abs center title-white" style="top:280px;font-size:35px">CONTAINERS</div>
    <div class="abs center subtitle" style="top:348px;font-size:29px"><span class="g">Eco Friendly</span> <span class="w">Wheatstraw</span></div>
    <div class="abs center compart" style="top:401px;font-size:24px">3 compartment</div>
    <svg class="abs" style="left:200px;top:449px" width="82" height="58" viewBox="0 0 43 30">
      <rect x="1" y="1" width="41" height="28" fill="none" stroke="var(--green)" stroke-width="1.2"/>
      <rect x="4" y="4" width="16" height="22" rx="4" fill="none" stroke="var(--green)" stroke-width="1.2"/>
      <rect x="23" y="4" width="16" height="10" rx="4" fill="none" stroke="var(--green)" stroke-width="1.2"/>
      <rect x="23" y="16" width="16" height="10" rx="4" fill="none" stroke="var(--green)" stroke-width="1.2"/>
      <g font-family="Archivo Black,sans-serif" font-size="7" fill="var(--white)" text-anchor="middle">
        <text x="12" y="18">2c</text><text x="31" y="12">1c</text><text x="31" y="24">1c</text>
      </g>
    </svg>
  </section>

  <section class="panel" style="left:809px;top:164px;width:363px;height:611px">
    <div class="pattern" role="img" aria-label="Faint food doodle pattern"></div>
    <div class="abs" style="left:0;right:0;top:272px;border-top:1px solid var(--cut)"></div>
    <div class="features" style="left:70px;top:36px;width:222px;height:209px">
      <div class="feature" style="font-size:6px"><svg width="40" height="40" viewBox="0 0 26 26"><circle cx="13" cy="13" r="11.5" fill="none" stroke="#fff" stroke-width="1.5"/><rect x="6" y="8" width="14" height="10" rx="1" fill="none" stroke="#fff"/></svg>Microwave Safe</div>
      <div class="feature" style="font-size:6px"><svg width="40" height="40" viewBox="0 0 26 26"><circle cx="13" cy="13" r="11.5" fill="none" stroke="#fff" stroke-width="1.5"/><path d="M13 5v16M6 9l14 8M6 17l14-8" stroke="#fff"/></svg>Freezer Safe</div>
      <div class="feature" style="font-size:6px"><svg width="40" height="40" viewBox="0 0 26 26"><circle cx="13" cy="13" r="11.5" fill="none" stroke="#fff" stroke-width="1.5"/><circle cx="11" cy="15" r="4" fill="none" stroke="#fff"/><circle cx="16" cy="15" r="4" fill="none" stroke="#fff"/></svg>Dishwasher Safe</div>
      <div class="feature" style="font-size:6px"><svg width="40" height="40" viewBox="0 0 26 26"><circle cx="13" cy="13" r="11.5" fill="none" stroke="#fff" stroke-width="1.5"/><text x="13" y="13" font-size="6" fill="#fff" text-anchor="middle" font-family="Open Sans,sans-serif">BPA</text><text x="13" y="19" font-size="5" fill="#fff" text-anchor="middle" font-family="Open Sans,sans-serif">FREE</text></svg>BPA Free</div>
      <div class="feature" style="font-size:6px"><svg width="40" height="40" viewBox="0 0 26 26"><circle cx="13" cy="13" r="11.5" fill="none" stroke="#fff" stroke-width="1.5"/><path d="M13 21V7M13 11l-3-3M13 14l3-3" stroke="#fff" fill="none"/></svg>Wheatstraw</div>
      <div class="feature" style="font-size:6px"><svg width="40" height="40" viewBox="0 0 26 26"><circle cx="13" cy="13" r="11.5" fill="none" stroke="#fff" stroke-width="1.5"/><path d="M13 7l5 9a5 5 0 0 1-10 0z" fill="none" stroke="#fff"/><path d="M5 19L21 7" stroke="#fff"/></svg>Leakproof</div>
      <div class="feature" style="font-size:6px"><svg width="40" height="40" viewBox="0 0 26 26"><circle cx="13" cy="13" r="11.5" fill="none" stroke="#fff" stroke-width="1.5"/><path d="M4 10h18M3 13h20M4 16h18" stroke="#fff"/></svg>Stackable</div>
      <div class="feature" style="font-size:6px"><svg width="40" height="40" viewBox="0 0 26 26"><circle cx="13" cy="13" r="11.5" fill="none" stroke="#fff" stroke-width="1.5"/><g fill="none" stroke="#fff" stroke-width=".8"><circle cx="8" cy="10" r="2.5"/><circle cx="13" cy="10" r="2.5"/><circle cx="18" cy="10" r="2.5"/><circle cx="8" cy="16" r="2.5"/><circle cx="13" cy="16" r="2.5"/><circle cx="18" cy="16" r="2.5"/></g></svg>Reusable</div>
      <div class="feature" style="font-size:6px"><svg width="40" height="40" viewBox="0 0 26 26"><circle cx="13" cy="13" r="11.5" fill="none" stroke="#fff" stroke-width="1.5"/><path d="M13 6l6 11H7z" fill="none" stroke="#fff" stroke-width="1.5"/></svg>Recycle</div>
    </div>
    <div class="brand-name dark" style="left:0;width:363px;top:415px;height:40px;font-size:28px"><span class="mark"></span>Lunchwell</div>
    <div class="web-band" style="top:549px;height:30px;line-height:30px;font-size:15px">www.lunchwell.com.au</div>
  </section>

</div>
</body>
</html>
```